Global Beard Oil Review Business needs a refresh

topwhiskertonic.net is a global business who's mission is to curate all available beard oils from around the world, review and grade them and present this curated collection to the user of the website.

The scope of this job includes the web site design and the design of a suitable logo to be used in the site header.

The existing site can be seen on http://topwhiskertonic.net, however this is a mock-up only the style and logo should NOT be used. This is to give you an idea of the concept of the site only.

This job is for PSD design only.

See attached design brief for detailed design requirements.
Updates

Project Deadline Extended
Reason: Extending deadline by 5 days to allow for final submissions

Target Market(s)

Men's grooming / retail

Industry/Entity Type

Retail

Number of Pages Required

2 page

Font styles to use
Sans Serif

Requirements
Must have
• 1) Comparison Table
• 2) Side Bar
• 3) Header area
• 4) Photo of Delvin Marsk (attached - can be circular or "cut-out")
• 5) Cool beard-oriented custom design background (e.g., stylistic black/brown on brown/orange beard background. I envision this beard background "drawing" rather than photo based)
• (see attached design requirements for details)
Nice to have
• Signature style writing at top with name "Delvin Marsk"
Should not have
• Do NOT use the look & feel or logo from the existing site.

```html
<!DOCTYPE html>
<html lang="en">
<head>
<meta charset="utf-8">
<title>Top Whisker Tonic</title>
<link rel="stylesheet" href="https://fonts.googleapis.com/css2?family=Amatic+SC:wght@400;700&family=Raleway:wght@400;500;600;700&display=swap">
<style>
:root{
  --page:#eef0f3;
  --panel:#f7f8fa;
  --white:#ffffff;
  --maroon:#6b0d0d;
  --maroon-dark:#4e0707;
  --orange:#f7a800;
  --orange-soft:#ffc94f;
  --hero:#ffcb6b;
  --cream:#fff1cf;
  --ink:#2a2a2a;
  --muted:#555;
  --line:#e2e2e2;
  --photo:#7a6a5c;
}
*{box-sizing:border-box;margin:0;padding:0}
html,body{width:1200px;height:2579px;overflow:hidden}
body{position:relative;background:var(--page);font-family:"Raleway",Arial,sans-serif;color:var(--ink)}
.abs{position:absolute}
.display{font-family:"Amatic SC","Arial Narrow",sans-serif;font-weight:700}

/* header */
.brand{left:77px;top:30px;display:flex;align-items:center;gap:12px}
.brand-dot{width:62px;height:62px;border-radius:50%;background:var(--ink)}
.brand-name{font-family:"Amatic SC",sans-serif;font-weight:700;font-size:44px;color:var(--ink);line-height:1;white-space:nowrap}
.contact{left:743px;top:28px;display:flex;align-items:center;gap:10px;font-size:15px;color:var(--ink)}
.contact-icon{width:26px;height:26px;border-radius:50%;background:var(--orange);display:flex;align-items:center;justify-content:center}
.social{display:flex;gap:10px}
.social span{width:28px;height:28px;border-radius:50%;background:var(--orange);display:block}
.social-top{left:985px;top:30px}
.nav{left:530px;top:86px;display:flex;align-items:center;font-size:16px;color:var(--ink)}
.nav a{color:inherit;text-decoration:none;padding:4px 10px}
.nav .current{background:var(--maroon);color:var(--white);padding:5px 12px}
.nav .sep{width:4px;height:4px;border-radius:50%;background:var(--ink);margin:0 6px}

/* hero */
.panel{left:79px;top:128px;width:1042px;height:827px;background:var(--panel)}
.hero{left:89px;top:138px;width:1022px;height:407px;background:var(--hero);overflow:hidden}
.hero-photo{left:35px;top:50px;width:340px;height:357px;background:linear-gradient(180deg,#8a7868,#4a3f38)}
.hero-badge{left:280px;top:85px;width:276px;height:276px;border-radius:50%;background:var(--cream);display:flex;flex-direction:column;align-items:center;justify-content:center;gap:10px}
.hero-badge .brand-name{font-size:38px}
.hero-badge .with{font-family:"Raleway",sans-serif;font-size:16px;font-weight:600;color:var(--ink)}
.hero-title{left:592px;top:78px;font-size:60px;line-height:83px;color:var(--ink);white-space:nowrap}
.hero-btn{left:595px;top:270px;width:145px;height:53px;background:var(--orange);color:var(--ink);font-size:22px;display:flex;align-items:center;justify-content:center}
.hero-dots{left:600px;top:338px;display:flex;gap:8px}
.hero-dots i{width:7px;height:7px;border-radius:50%;background:var(--white);display:block}
.hero-dots i.on{background:var(--orange)}

/* welcome */
.welcome-title{left:79px;top:568px;width:1042px;text-align:center;font-size:64px;color:var(--ink)}
.welcome-title em{font-style:normal;color:var(--maroon)}
.welcome-text{left:155px;top:652px;width:890px;text-align:center;font-size:12.5px;line-height:20px;color:var(--muted)}
.steps{left:79px;top:770px;width:1042px;height:180px}
.step-label{font-size:30px;color:var(--ink);text-align:center;width:200px}

/* comparison table */
.compare{left:79px;top:987px;width:781px;border-collapse:collapse;background:var(--white);box-shadow:0 1px 4px rgba(0,0,0,.15);table-layout:fixed}
.compare th{height:62px;font-size:11px;font-weight:700;vertical-align:middle;border-right:1px solid rgba(255,255,255,.35)}
.compare th.key{background:var(--maroon);color:var(--orange);text-align:left;padding:0 8px}
.compare th.score{background:var(--orange);color:var(--maroon);position:relative;overflow:hidden}
.compare th .rot{position:absolute;left:0;right:0;top:16px;text-align:center;transform:rotate(-35deg);white-space:nowrap;font-size:10px}
.compare th .arrow{position:absolute;bottom:6px;left:0;right:0;text-align:center;font-size:9px}
.compare th .stack{font-size:9px;line-height:11px;text-align:center;display:block}
.filter{display:block;margin-top:5px;background:var(--maroon-dark);border:1px solid #220;color:var(--white);font-size:9px;font-weight:500;padding:1px 4px;width:150px}
.compare td{height:90px;border-bottom:1px solid var(--line);border-right:1px solid var(--line);font-size:12px;text-align:center;vertical-align:middle}
.supplier{display:flex;align-items:center;gap:14px;text-align:left;padding-left:12px}
.thumb{width:40px;height:52px;flex:none;background:linear-gradient(180deg,#f4c64a,#c88a1a)}
.thumb.dark{width:26px;background:linear-gradient(180deg,#a05a3a,#5a2a18);margin:0 7px}
.supplier b{display:block;color:var(--maroon);font-size:15px;line-height:17px}
.supplier small{display:block;font-size:12px;color:var(--muted);margin-top:2px}
.buy{display:inline-block;background:var(--orange);color:var(--white);font-size:12px;padding:5px 8px}
.loading{left:394px;top:2441px;width:153px;height:34px;background:#2e2e2e;color:var(--white);font-size:14px;display:flex;align-items:center;justify-content:center;gap:8px;border-radius:3px}

/* sidebar */
.subscribe{left:885px;top:987px;width:234px;height:340px;background:var(--orange);text-align:center;padding:16px 20px}
.subscribe h2{font-size:34px;line-height:1.05;color:var(--maroon)}
.subscribe p{font-size:12px;line-height:16px;color:var(--ink);margin-top:18px}
.subscribe .field{background:var(--white);height:36px;margin-top:16px;font-size:11px;color:#999;display:flex;align-items:center;justify-content:center}
.subscribe .go{background:var(--maroon);color:var(--white);height:36px;margin-top:14px;font-size:13px;font-weight:700;display:flex;align-items:center;justify-content:center}
.subscribe .note{font-size:10px;color:var(--white);margin-top:14px}
.blog-title{left:885px;top:1378px;font-size:40px;color:var(--ink)}
.post{left:885px;width:234px}
.post-img{width:234px;height:155px;border:2px solid var(--white);box-shadow:0 1px 3px rgba(0,0,0,.25)}
.post h3{font-size:15px;line-height:16px;color:var(--orange);margin-top:12px;font-weight:700}
.post time{display:block;font-size:12px;color:var(--ink);margin-top:3px;padding-left:3px}

/* footer */
.footer{left:0;top:2518px;width:1200px;height:61px;background:var(--orange)}
.footer-links{left:80px;top:10px;font-size:13px;color:var(--ink);display:flex;gap:6px}
.footer-rule{left:80px;top:32px;width:800px;height:1px;background:rgba(0,0,0,.2)}
.copyright{left:80px;top:38px;font-size:11px;color:var(--maroon)}
.social-foot{left:934px;top:16px}
.social-foot span{background:transparent;border:2px solid var(--ink)}
</style>
</head>
<body>

<header>
  <div class="abs brand"><span class="brand-dot"></span><span class="brand-name">Top Whisker Tonic</span></div>
  <div class="abs contact">
    <span class="contact-icon"><svg width="14" height="10" viewBox="0 0 14 10"><rect x=".5" y=".5" width="13" height="9" fill="none" stroke="#2a2a2a"/><path d="M.5 .5 7 6l6.5-5.5" fill="none" stroke="#2a2a2a"/></svg></span>
    info@topwhiskertonic.net
  </div>
  <div class="abs social social-top"><span></span><span></span><span></span><span></span></div>
  <nav class="abs nav">
    <a class="current">Home</a><a>About</a><i class="sep"></i><a>Our Charter</a><i class="sep"></i><a>Beard Oil Review Methodology</a><i class="sep"></i><a>Blog</a>
  </nav>
</header>

<div class="abs panel"></div>

<section class="abs hero">
  <div class="abs hero-photo" role="img" aria-label="Cut-out photo of Delvin Marsk giving a thumbs up"></div>
  <div class="abs hero-badge">
    <span class="brand-name">Top Whisker Tonic</span>
    <span class="with">-With Delvin Marsk</span>
  </div>
  <h1 class="abs hero-title display">Curate, Review &amp; Grade<br>Then Present</h1>
  <div class="abs hero-btn">See Table</div>
  <div class="abs hero-dots"><i></i><i></i><i></i><i class="on"></i></div>
</section>

<section>
  <h2 class="abs welcome-title display">Welcome To <em>Top Whisker Tonic</em></h2>
  <p class="abs welcome-text">We are a global business with the mission is to curate all available beard oils from around the world, review &amp; grade them &amp; present this curated collection to the users of the site. Our Target Audience are all grooming men. Lorem ipsum dolor sit amet, consectetuer adipiscing elit, sed diam nonummy nibh euismod tincidunt ut laoreet dolore magna aliquam erat volutpat. Lorem ipsum dolor sit amet, consectetuer adipiscing elit, sed diam nonummy nibh euismod tincidunt ut laoreet dolore magna aliquam erat volutpat.</p>
  <svg class="abs steps" viewBox="0 0 1042 180" width="1042" height="180">
    <path id="arcA" d="M200 100 Q330 160 460 90" fill="none" stroke="#6b0d0d" stroke-width="1.5" stroke-dasharray="2 4"/>
    <path id="arcB" d="M570 45 Q730 -30 860 45" fill="none" stroke="#6b0d0d" stroke-width="1.5" stroke-dasharray="2 4"/>
    <path id="arcAt" d="M200 88 Q330 148 460 78" fill="none"/>
    <path id="arcBt" d="M570 35 Q730 -40 860 35" fill="none"/>
    <text font-family="Raleway,sans-serif" font-size="13" fill="#6b0d0d"><textPath href="#arcAt" startOffset="14%">We curate all available beard oils</textPath></text>
    <text font-family="Raleway,sans-serif" font-size="13" fill="#6b0d0d"><textPath href="#arcBt" startOffset="10%">Review &amp; Grade them &amp; Present</textPath></text>
    <circle cx="146" cy="65" r="55" fill="#f7a800"/>
    <circle cx="519" cy="65" r="55" fill="#f7a800"/>
    <circle cx="894" cy="65" r="55" fill="#f7a800"/>
    <path d="M131 48v30h30v-22h-8v-10h-8v10h-14z" fill="#6b0d0d"/>
    <path d="M519 38l7 16 17 1-13 11 4 17-15-9-15 9 4-17-13-11 17-1z" fill="#6b0d0d"/>
    <rect x="868" y="43" width="52" height="40" fill="none" stroke="#6b0d0d" stroke-width="4"/>
    <path d="M868 52h52M894 90V62m-10 10 10-10 10 10" fill="none" stroke="#6b0d0d" stroke-width="4"/>
  </svg>
  <div class="abs step-label display" style="left:125px;top:900px">Curate</div>
  <div class="abs step-label display" style="left:498px;top:900px">Review &amp; Grade</div>
  <div class="abs step-label display" style="left:873px;top:900px">Present</div>
</section>

<table class="abs compare">
  <colgroup><col style="width:191px"><col style="width:72px"><col style="width:91px"><col style="width:100px"><col style="width:45px"><col style="width:48px"><col style="width:48px"><col style="width:45px"><col style="width:81px"><col style="width:60px"></colgroup>
  <thead><tr>
    <th class="key">Product Supplier<span class="filter">Bristle Baron &nbsp;&nbsp;&nbsp;&nbsp;&nbsp;&nbsp;&nbsp;&nbsp;&nbsp;&nbsp;&nbsp;&nbsp;&nbsp;▾</span></th>
    <th class="key">Origin ▾</th>
    <th class="key">Base Oil ▾</th>
    <th class="key">Scent ▾</th>
    <th class="score"><span class="rot">Aroma</span><span class="arrow">▼</span></th>
    <th class="score"><span class="rot">Therapy</span><span class="arrow">▼</span></th>
    <th class="score"><span class="rot">Value</span><span class="arrow">▼</span></th>
    <th class="score"><span class="rot">Over All</span><span class="arrow">▼</span></th>
    <th class="score">Get It</th>
    <th class="score"><span class="stack">Delvin<br>Marsk<br>Recommend</span></th>
  </tr></thead>
  <tbody>
    <tr><td><div class="supplier"><span class="thumb" role="img" aria-label="Product box photo"></span><div><b>Trail-Kit</b><small>-Bristle Baron</small></div></div></td><td>USA</td><td>Jojoba,</td><td>Spice Market</td><td>5</td><td>5</td><td>5</td><td>5</td><td><span class="buy">Buy Now</span></td><td><svg width="16" height="16" viewBox="0 0 16 16"><path d="M1 7h3v8H1zM5 7l4-6c2 0 2 2 1 5h5l-1 9H5z" fill="#6b0d0d"/></svg></td></tr>
    <tr><td><div class="supplier"><span class="thumb dark" role="img" aria-label="Product bottle photo"></span><div><b>Harbor Lane<br>Tobacco</b><small>-Bristle Baron</small></div></div></td><td>USA</td><td>Jojoba,</td><td>Spice Market</td><td>5</td><td>5</td><td>5</td><td>5</td><td><span class="buy">Buy Now</span></td><td><svg width="16" height="16" viewBox="0 0 16 16"><path d="M1 7h3v8H1zM5 7l4-6c2 0 2 2 1 5h5l-1 9H5z" fill="#6b0d0d"/></svg></td></tr>
    <tr><td><div class="supplier"><span class="thumb" role="img" aria-label="Product box photo"></span><div><b>Trail-Kit</b><small>-Bristle Baron</small></div></div></td><td>USA</td><td>Jojoba,</td><td>Spice Market</td><td>5</td><td>5</td><td>5</td><td>5</td><td><span class="buy">Buy Now</span></td><td><svg width="16" height="16" viewBox="0 0 16 16"><path d="M1 7h3v8H1zM5 7l4-6c2 0 2 2 1 5h5l-1 9H5z" fill="#6b0d0d"/></svg></td></tr>
    <tr><td><div class="supplier"><span class="thumb dark" role="img" aria-label="Product bottle photo"></span><div><b>Harbor Lane<br>Tobacco</b><small>-Bristle Baron</small></div></div></td><td>USA</td><td>Jojoba,</td><td>Spice Market</td><td>5</td><td>5</td><td>5</td><td>5</td><td><span class="buy">Buy Now</span></td><td><svg width="16" height="16" viewBox="0 0 16 16"><path d="M1 7h3v8H1zM5 7l4-6c2 0 2 2 1 5h5l-1 9H5z" fill="#6b0d0d"/></svg></td></tr>
    <tr><td><div class="supplier"><span class="thumb" role="img" aria-label="Product box photo"></span><div><b>Trail-Kit</b><small>-Bristle Baron</small></div></div></td><td>USA</td><td>Jojoba,</td><td>Spice Market</td><td>5</td><td>5</td><td>5</td><td>5</td><td><span class="buy">Buy Now</span></td><td><svg width="16" height="16" viewBox="0 0 16 16"><path d="M1 7h3v8H1zM5 7l4-6c2 0 2 2 1 5h5l-1 9H5z" fill="#6b0d0d"/></svg></td></tr>
    <tr><td><div class="supplier"><span class="thumb dark" role="img" aria-label="Product bottle photo"></span><div><b>Harbor Lane<br>Tobacco</b><small>-Bristle Baron</small></div></div></td><td>USA</td><td>Jojoba,</td><td>Spice Market</td><td>5</td><td>5</td><td>5</td><td>5</td><td><span class="buy">Buy Now</span></td><td><svg width="16" height="16" viewBox="0 0 16 16"><path d="M1 7h3v8H1zM5 7l4-6c2 0 2 2 1 5h5l-1 9H5z" fill="#6b0d0d"/></svg></td></tr>
    <tr><td><div class="supplier"><span class="thumb" role="img" aria-label="Product box photo"></span><div><b>Trail-Kit</b><small>-Bristle Baron</small></div></div></td><td>USA</td><td>Jojoba,</td><td>Spice Market</td><td>5</td><td>5</td><td>5</td><td>5</td><td><span class="buy">Buy Now</span></td><td><svg width="16" height="16" viewBox="0 0 16 16"><path d="M1 7h3v8H1zM5 7l4-6c2 0 2 2 1 5h5l-1 9H5z" fill="#6b0d0d"/></svg></td></tr>
    <tr><td><div class="supplier"><span class="thumb dark" role="img" aria-label="Product bottle photo"></span><div><b>Harbor Lane<br>Tobacco</b><small>-Bristle Baron</small></div></div></td><td>USA</td><td>Jojoba,</td><td>Spice Market</td><td>5</td><td>5</td><td>5</td><td>5</td><td><span class="buy">Buy Now</span></td><td><svg width="16" height="16" viewBox="0 0 16 16"><path d="M1 7h3v8H1zM5 7l4-6c2 0 2 2 1 5h5l-1 9H5z" fill="#6b0d0d"/></svg></td></tr>
    <tr><td><div class="supplier"><span class="thumb" role="img" aria-label="Product box photo"></span><div><b>Trail-Kit</b><small>-Bristle Baron</small></div></div></td><td>USA</td><td>Jojoba,</td><td>Spice Market</td><td>5</td><td>5</td><td>5</td><td>5</td><td><span class="buy">Buy Now</span></td><td><svg width="16" height="16" viewBox="0 0 16 16"><path d="M1 7h3v8H1zM5 7l4-6c2 0 2 2 1 5h5l-1 9H5z" fill="#6b0d0d"/></svg></td></tr>
    <tr><td><div class="supplier"><span class="thumb dark" role="img" aria-label="Product bottle photo"></span><div><b>Harbor Lane<br>Tobacco</b><small>-Bristle Baron</small></div></div></td><td>USA</td><td>Jojoba,</td><td>Spice Market</td><td>5</td><td>5</td><td>5</td><td>5</td><td><span class="buy">Buy Now</span></td><td><svg width="16" height="16" viewBox="0 0 16 16"><path d="M1 7h3v8H1zM5 7l4-6c2 0 2 2 1 5h5l-1 9H5z" fill="#6b0d0d"/></svg></td></tr>
    <tr><td><div class="supplier"><span class="thumb" role="img" aria-label="Product box photo"></span><div><b>Trail-Kit</b><small>-Bristle Baron</small></div></div></td><td>USA</td><td>Jojoba,</td><td>Spice Market</td><td>5</td><td>5</td><td>5</td><td>5</td><td><span class="buy">Buy Now</span></td><td><svg width="16" height="16" viewBox="0 0 16 16"><path d="M1 7h3v8H1zM5 7l4-6c2 0 2 2 1 5h5l-1 9H5z" fill="#6b0d0d"/></svg></td></tr>
    <tr><td><div class="supplier"><span class="thumb dark" role="img" aria-label="Product bottle photo"></span><div><b>Harbor Lane<br>Tobacco</b><small>-Bristle Baron</small></div></div></td><td>USA</td><td>Jojoba,</td><td>Spice Market</td><td>5</td><td>5</td><td>5</td><td>5</td><td><span class="buy">Buy Now</span></td><td><svg width="16" height="16" viewBox="0 0 16 16"><path d="M1 7h3v8H1zM5 7l4-6c2 0 2 2 1 5h5l-1 9H5z" fill="#6b0d0d"/></svg></td></tr>
    <tr><td><div class="supplier"><span class="thumb" role="img" aria-label="Product box photo"></span><div><b>Trail-Kit</b><small>-Bristle Baron</small></div></div></td><td>USA</td><td>Jojoba,</td><td>Spice Market</td><td>5</td><td>5</td><td>5</td><td>5</td><td><span class="buy">Buy Now</span></td><td><svg width="16" height="16" viewBox="0 0 16 16"><path d="M1 7h3v8H1zM5 7l4-6c2 0 2 2 1 5h5l-1 9H5z" fill="#6b0d0d"/></svg></td></tr>
    <tr><td><div class="supplier"><span class="thumb dark" role="img" aria-label="Product bottle photo"></span><div><b>Harbor Lane<br>Tobacco</b><small>-Bristle Baron</small></div></div></td><td>USA</td><td>Jojoba,</td><td>Spice Market</td><td>5</td><td>5</td><td>5</td><td>5</td><td><span class="buy">Buy Now</span></td><td><svg width="16" height="16" viewBox="0 0 16 16"><path d="M1 7h3v8H1zM5 7l4-6c2 0 2 2 1 5h5l-1 9H5z" fill="#6b0d0d"/></svg></td></tr>
    <tr><td><div class="supplier"><span class="thumb" role="img" aria-label="Product box photo"></span><div><b>Trail-Kit</b><small>-Bristle Baron</small></div></div></td><td>USA</td><td>Jojoba,</td><td>Spice Market</td><td>5</td><td>5</td><td>5</td><td>5</td><td><span class="buy">Buy Now</span></td><td><svg width="16" height="16" viewBox="0 0 16 16"><path d="M1 7h3v8H1zM5 7l4-6c2 0 2 2 1 5h5l-1 9H5z" fill="#6b0d0d"/></svg></td></tr>
  </tbody>
</table>

<div class="abs loading"><svg width="16" height="16" viewBox="0 0 16 16"><path d="M8 2a6 6 0 1 0 6 6" fill="none" stroke="#fff" stroke-width="2"/></svg>Loading More...</div>

<aside>
  <div class="abs subscribe">
    <h2 class="display">Get More Stuff Like This In Your InBox</h2>
    <p>Subscribe to our mailing list &amp; get interesting stuff &amp; updates.</p>
    <div class="field">Enter your email here</div>
    <div class="go">SIGNUP NOW</div>
    <p class="note">We respect your privacy and take protecting it seriously.</p>
  </div>
  <h2 class="abs blog-title display">Latest Blog</h2>
  <article class="abs post" style="top:1453px">
    <div class="post-img" role="img" aria-label="Photo of a beard oil pouch on a wooden table" style="background:linear-gradient(135deg,#c98a4a,#8a5428)"></div>
    <h3>Ridge Runner Beard Oil by Old Oak Grooming</h3><time>February 12, 2016</time>
  </article>
  <article class="abs post" style="top:1710px">
    <div class="post-img" role="img" aria-label="Photo of a dropper bottle outdoors" style="background:linear-gradient(135deg,#6b7a4a,#2e3a22)"></div>
    <h3>Outback Face/Beard Oil by Fernleaf Soaps</h3><time>February 9, 2016</time>
  </article>
  <article class="abs post" style="top:1960px">
    <div class="post-img" role="img" aria-label="Photo of a wrapped beard oil bottle" style="background:linear-gradient(135deg,#d8c8a8,#9a8466)"></div>
    <h3>Chopshop Beard Oil by Chopshop Men's Grooming</h3><time>January 25, 2016</time>
  </article>
  <article class="abs post" style="top:2209px">
    <div class="post-img" role="img" aria-label="Photo of a small beard oil bottle with packaging" style="background:linear-gradient(135deg,#b9b4a8,#5e574c)"></div>
    <h3>Timberman Oil by Crossroad Beard Co.</h3><time>January 10, 2016</time>
  </article>
</aside>

<footer class="abs footer">
  <div class="abs footer-links"><span>Home</span>|<span>About</span>|<span>Our Charter</span>|<span>Beard Oil Review Methodology</span>|<span>Blog</span>|<span>Terms And Conditions</span>|<span>Disclaimer</span>|<span>Privacy Policy</span></div>
  <div class="abs footer-rule"></div>
  <div class="abs copyright">Copyright 2016 Top Whisker Tonic. All Rights Reserved</div>
  <div class="abs social social-foot"><span></span><span></span><span></span><span></span></div>
</footer>

</body>
</html>
```